Lifecoach needs website design based on a standard Wordpress theme

I need a website for my new lifecoaching business that can be easily implemented in Wordpress, it needs to be compatible with a standard Wordpress theme. So I can place the pictures, texts etc. in a standard theme of Wordpress.

I want the design to be a very good feeling and playfull one, based on my logo.

Target Market(s)

I will coach people to reach their goals and dreams in life.

Industry/Entity Type

Business

Requirements
Must have
• Can be easy implemented in Wordpress.
Nice to have
• Photo's of nature are nice.

```html
<!DOCTYPE html>
<html lang="en">
<head>
<meta charset="utf-8">
<title>Ruben Olde Koster Lifecoach</title>
<link href="https://fonts.googleapis.com/css2?family=Source+Sans+3:ital,wght@0,300;0,400;0,600;0,700;1,400&display=swap" rel="stylesheet">
<style>
:root{
  --blue:#2f8ad6;
  --blue-light:#4aa6ea;
  --blue-dark:#1f6fb6;
  --heading:#1b5a8f;
  --text:#7c8a96;
  --band:#1d5f8e;
  --footer:#0f3d66;
  --line:#d9dee2;
  --page:#fbfcfd;
}
*{margin:0;padding:0;box-sizing:border-box}
html,body{width:933px;height:1200px;overflow:hidden;background:var(--page);font-family:"Source Sans 3",sans-serif;color:var(--text)}
.canvas{position:relative;width:933px;height:1200px}
.abs{position:absolute}

.topbar{left:0;top:0;width:933px;height:51px;background:#fff}
.contact-top{top:20px;font-size:8.5px;color:var(--blue-dark);display:flex;align-items:center;gap:6px}
.nav-band{left:0;top:51px;width:933px;height:36px;background:linear-gradient(#4aa3e8,#2f86d2);border-bottom:1px solid #2270b5}
.nav{left:476px;top:51px;height:36px;display:flex}
.nav a{display:flex;align-items:center;justify-content:center;height:36px;color:#fff;font-weight:700;font-size:10px;text-decoration:none;border-left:1px solid #2a7cc4;border-right:1px solid #5ab0ee}
.nav a.active{background:#2a79be}

.logo-box{left:124px;top:0;width:292px;height:109px;background:linear-gradient(#ffffff,#ececec);border-radius:0 0 6px 6px;box-shadow:0 2px 5px rgba(0,0,0,.2);z-index:3;display:flex;align-items:center;padding-left:20px;gap:12px}
.logo-dot{width:62px;height:62px;border-radius:50%;background:var(--blue)}
.logo-name{color:var(--heading);font-size:17px;font-weight:400;line-height:1.2;letter-spacing:.5px}

.hero{left:0;top:87px;width:933px;height:554px;background:
  radial-gradient(ellipse 220px 160px at 590px 40px,rgba(240,250,160,.9),transparent),
  radial-gradient(ellipse 200px 300px at 330px 330px,rgba(225,235,240,.55),transparent),
  linear-gradient(160deg,#5e9a28 0%,#8cc23b 40%,#4f8d1e 75%,#3e7a18 100%)}
.hero-title{left:535px;top:266px;width:300px;color:#fff;font-weight:700;font-size:25px;line-height:32px;text-shadow:0 1px 3px rgba(0,0,0,.35)}
.hero-text{left:538px;top:340px;width:280px;color:#fff;font-size:13px;line-height:16px;text-shadow:0 1px 2px rgba(0,0,0,.35)}
.hero-dots{left:755px;top:475px;display:flex;gap:4px}
.hero-dots span{width:6px;height:6px;border-radius:50%;background:#9fd05a}
.hero-dots span.on{background:#1f8ad8}

.card{top:518px;width:219px;height:265px;background:#fff;border:1px solid #d5dade;box-shadow:0 1px 2px rgba(0,0,0,.06)}
.card h2{font-weight:400;font-size:17.5px;color:var(--heading);text-align:center;margin-top:14px}
.card .photo{margin:9px auto 0;width:197px;height:102px}
.card p{font-size:8.5px;line-height:14.5px;padding:0 11px;margin-top:13px}
.btn{display:inline-flex;align-items:center;justify-content:center;gap:5px;height:28px;border:1px solid #c9cfd4;border-radius:14px;background:linear-gradient(#fff,#eef0f2);font-size:8.5px;color:#8a96a0}
.card .btn{position:absolute;left:11px;top:213px;width:80px}
.field{position:absolute;left:19px;width:185px;height:27px;border:1px solid #dde1e4;font-size:8px;color:#6b7780;padding:9px 10px}
.note{position:absolute;left:22px;top:184px;font-size:7.5px;color:#8a96a0}

.section-title{top:805px;font-size:17.5px;font-weight:400;color:var(--heading)}
.divider{top:837px;height:4px;border-top:1px solid var(--line);border-bottom:1px solid var(--line)}
.coach-photo{left:127px;top:850px;width:217px;height:153px;background:linear-gradient(90deg,#c9a183 0%,#b8c6d6 55%,#eef0f1 90%)}
.coach-text{left:360px;top:864px;width:205px;font-size:8.5px;line-height:13px}
.coach-text p+p{margin-top:13px}
.avatar{left:660px;top:852px;width:64px;height:64px;border-radius:50%;background:linear-gradient(#6b4a3a,#c9a18a)}
.t-name{left:590px;top:926px;width:204px;text-align:center;font-size:10.5px;color:#7d8a96}
.t-place{left:590px;top:941px;width:204px;text-align:center;font-size:8.5px;color:#5e6c78}
.t-quote{left:600px;top:959px;width:190px;font-size:8.5px;line-height:14.5px;font-style:italic;color:#98a4ad}

.cta{left:0;top:1052px;width:933px;height:71px;background:var(--band);border-top:3px solid #2f7bb3}
.cta-text{left:124px;top:1077px;font-weight:700;font-size:16.5px;color:#fff}
.cta-btn{left:633px;top:1070px;width:181px;height:39px;border-radius:5px;background:linear-gradient(#3aaef0,#1e8cd6);border:1px solid #7fcaf5;color:#fff;font-weight:700;font-size:12px;display:flex;align-items:center;justify-content:center}
.footer{left:0;top:1123px;width:933px;height:77px;background:var(--footer)}
.f-links{left:131px;top:1141px;font-size:8px;font-weight:700;color:#fff;letter-spacing:.3px}
.f-copy{left:130px;top:1163px;font-size:8px;color:#fff}
.social{top:1138px;width:20px;height:20px;border-radius:50%;background:#fff}
.f-contact{left:652px;font-size:8px;font-weight:700;color:#fff;display:flex;align-items:center;gap:12px}
</style>
</head>
<body>
<div class="canvas">
  <div class="abs topbar"></div>
  <div class="abs contact-top" style="left:612px">
    <svg width="22" height="11" viewBox="0 0 22 11"><g fill="none" stroke="#4a9ad8" stroke-width="1"><line x1="0" y1="3" x2="5" y2="3"/><line x1="1" y1="6" x2="5" y2="6"/><rect x="7" y="1" width="14" height="9"/><polyline points="7,1 14,6 21,1"/></g></svg>
    hello@ruboldekoster.com
  </div>
  <div class="abs contact-top" style="left:733px">
    <svg width="11" height="12" viewBox="0 0 11 12"><path d="M2 1 L4 1 L5 4 L3.5 5 Q5 8 7 9 L8 7.5 L11 8.5 L11 10.5 Q6 12 2 6 Q0.5 3 2 1Z" fill="none" stroke="#4a9ad8"/></svg>
    +31 20 555 0148
  </div>

  <div class="abs nav-band"></div>
  <nav class="abs nav">
    <a class="active" style="width:66px">Home</a>
    <a style="width:65px">About</a>
    <a style="width:65px">Coaching</a>
    <a style="width:73px">Articles</a>
    <a style="width:65px">Contact</a>
  </nav>

  <div class="abs logo-box">
    <div class="logo-dot"></div>
    <div class="logo-name">RUBEN OLDE KOSTER<br>LIFECOACH</div>
  </div>

  <div class="abs hero" role="img" aria-label="Woman with raised arms in a sunlit green meadow"></div>
  <h1 class="abs hero-title">Make your life be what you want it to be!</h1>
  <p class="abs hero-text">Lorem ipsum dolor sit amet, consectetur adipisicing elit, sed do eiusmod tempor incididunt ut labore et dolore magna aliqua.</p>
  <div class="abs hero-dots"><span class="on"></span><span></span></div>

  <section class="abs card" style="left:124px">
    <h2>What is Life Coaching?</h2>
    <div class="photo" role="img" aria-label="Two women talking in a bright room" style="background:linear-gradient(90deg,#6e5a48,#e6e4e0 45%,#f3f2ef 70%,#d8c8b8)"></div>
    <p>Lorem ipsum dolor sit amet, consectetur adipisicing elit, sed do eiusmod tempor incididunt ut labore et dolore magna aliqua.</p>
    <span class="btn">Read More ›</span>
  </section>

  <section class="abs card" style="left:358px">
    <h2>Life Advices</h2>
    <div class="photo" role="img" aria-label="Couple sitting outdoors in the greenery" style="background:linear-gradient(90deg,#8fae5a,#d9d3c6 40%,#7e9a45 70%,#b9c47a)"></div>
    <p>Lorem ipsum dolor sit amet, consectetur adipisicing elit, sed do eiusmod tempor incididunt ut labore et dolore magna aliqua.</p>
    <span class="btn">Read More ›</span>
  </section>

  <section class="abs card" style="left:590px">
    <h2>Sign up for Newsletter</h2>
    <p style="margin-top:16px;padding:0 22px">Lorem ipsum dolor sit amet, consectetur adipisicing elit, sed do eiusmod tempor incididunt ut labore et dolore magna aliqua.</p>
    <div class="field" style="top:102px">Your Name</div>
    <div class="field" style="top:140px">Your Email</div>
    <div class="note">*Your email will be held in strictest confidentiality.</div>
    <span class="btn" style="position:absolute;left:19px;top:213px;width:80px">Submit Now</span>
  </section>

  <h2 class="abs section-title" style="left:128px">Meet Your Life Coach</h2>
  <div class="abs divider" style="left:125px;width:438px"></div>
  <div class="abs coach-photo" role="img" aria-label="Portrait of the life coach smiling"></div>
  <div class="abs coach-text">
    <p>Tempor incididunt ut labore et dolore magna aliqua. Ut enim ad minim veniam, quis nostrud exercitation. Lorem ipsum dolor sit amet, consectetur adipisicing elit, sed do eiusmod</p>
    <p>Lorem ipsum dolor sit amet, consectetur adipisicing elit, sed do eiusmod</p>
  </div>
  <span class="abs btn" style="left:360px;top:975px;width:80px">Read More ›</span>

  <h2 class="abs section-title" style="left:591px">Client Testimonial</h2>
  <div class="abs divider" style="left:590px;width:218px"></div>
  <div class="abs avatar" role="img" aria-label="Portrait of client"></div>
  <div class="abs t-name">Mara Lindqvist</div>
  <div class="abs t-place">Paris, France</div>
  <p class="abs t-quote">"Lorem ipsum dolor sit amet, consectetur adipisicing elit, sed do eiusmod tempor incididunt ut labore et dolore magna aliqua."</p>

  <div class="abs cta"></div>
  <div class="abs cta-text">Life life to the fullest. Book a Private Coaching Session Now.</div>
  <div class="abs cta-btn">Request Coaching Session</div>

  <footer class="abs footer"></footer>
  <div class="abs f-links">LINKS &nbsp;| &nbsp;LINKS &nbsp;| &nbsp;LINKS &nbsp;| &nbsp;LINKS</div>
  <div class="abs f-copy">Copyright © 2014. All rights reserved. &nbsp;Company Name. Privacy Policy &nbsp;| &nbsp;Sitemap</div>
  <div class="abs social" style="left:539px"></div>
  <div class="abs social" style="left:568px"></div>
  <div class="abs social" style="left:597px"></div>
  <div class="abs f-contact" style="top:1140px">
    <svg width="14" height="10" viewBox="0 0 14 10"><rect width="14" height="10" fill="#2f86d2"/><polyline points="0,0 7,6 14,0" fill="none" stroke="#0f3d66"/></svg>
    info@brightpathcoach.com
  </div>
  <div class="abs f-contact" style="top:1161px">
    <svg width="14" height="12" viewBox="0 0 11 12"><path d="M2 1 L4 1 L5 4 L3.5 5 Q5 8 7 9 L8 7.5 L11 8.5 L11 10.5 Q6 12 2 6 Q0.5 3 2 1Z" fill="#2f86d2"/></svg>
    020-555-01877
  </div>
</div>
</body>
</html>
```